BRIGHTHOLD PROPERTY MANAGEMENT INC. WEBSITE

Please make the website more family-friendly.

I want a website to help me build my property management business by adding listing properties and creating an online application. Im open to any other ideas.
I want a WordPress designer to code it.

Here is my current website. www.brighthold.biz

IDEA: I like the website design https://www.pelicanclimateservices.com/

Thank you

Tom

Number of Pages Required

5+ page

```html
<!DOCTYPE html>
<html lang="en">
<head>
<meta charset="utf-8">
<title>Brighthold Property Management Inc.</title>
<link rel="stylesheet" href="https://fonts.googleapis.com/css2?family=Lora:wght@600;700&family=Arimo:wght@400;700&display=swap">
<style>
:root{
  --red:#a50d12;
  --red-dark:#8e0a0f;
  --ink:#1d1d1d;
  --muted:#555;
  --pale:#d9dcd9;
  --white:#fff;
}
*{box-sizing:border-box;margin:0;padding:0}
html,body{width:1200px;height:4140px;overflow:hidden}
body{position:relative;font-family:"Arimo",Arial,sans-serif;color:var(--ink);background:var(--white)}
.abs{position:absolute}
.serif{font-family:"Lora",Georgia,serif}
.btn{position:absolute;background:var(--red);color:#fff;font-size:15px;display:flex;align-items:center;justify-content:center;gap:8px;border-radius:3px}
.btn-ghost{background:#fff;color:var(--red)}

/* header */
.site-header{position:absolute;left:0;top:0;width:1200px;height:120px;background:#fff}
.brand{position:absolute;left:108px;top:20px;width:145px;text-align:center;color:var(--red)}
.brand .mark{width:40px;height:40px;background:var(--red);border-radius:50%;margin:0 auto 6px}
.brand .name{font-family:"Lora",serif;font-weight:700;font-size:17px;letter-spacing:.5px}
.brand .sub{font-size:6px;letter-spacing:.4px}
.main-nav{position:absolute;left:297px;top:84px;display:flex;gap:26px;font-size:14px;color:#333}
.main-nav span::after{content:" \25BE";font-size:12px}

/* hero */
.hero{position:absolute;left:0;top:120px;width:1200px;height:642px;background:linear-gradient(160deg,#23428a 0%,#1a2e5e 40%,#5a2a1c 65%,#c2391c 80%,#1a1a22 100%)}
.hero-box{position:absolute;left:306px;top:203px;width:568px;height:294px;border:2px solid rgba(255,255,255,.7);border-radius:8px;background:rgba(20,30,50,.55);text-align:center;color:#fff}
.hero-box h1{font-family:"Lora",serif;font-size:44px;margin-top:30px;letter-spacing:1px}
.hero-box p{font-size:25px;line-height:41px;margin-top:6px}
.dots{position:absolute;left:561px;top:518px;display:flex;gap:8px}
.dots i{width:9px;height:9px;background:rgba(255,255,255,.4)}
.dots i.on{background:#fff}

/* services */
.section-title{position:absolute;left:0;width:1200px;text-align:center;font-family:"Lora",serif;font-weight:700;color:var(--red);letter-spacing:1px}
.service{position:absolute;top:900px;width:200px;text-align:center}
.service svg{display:block;margin:0 auto}
.service h3{margin-top:22px;color:var(--red);font-size:21px;font-weight:700;letter-spacing:.5px}

/* about */
.about{position:absolute;left:0;top:1192px;width:1200px;height:618px;background:var(--pale)}
.about-photo{position:absolute;left:0;top:0;width:567px;height:618px;background:linear-gradient(180deg,#eee 0%,#d2d0cc 60%,#bdb8b0 100%)}
.about-text{position:absolute;left:598px;top:50px;width:500px}
.about-text h2{font-family:"Lora",serif;color:var(--red);font-size:36px;letter-spacing:1px}
.about-text p{font-size:13.5px;line-height:26px;color:#444;margin-top:16px}
.about-text .cta{font-size:20px;font-weight:700;line-height:31px;margin-top:26px;color:#111}
.about-text .cta em{font-style:normal;color:var(--red)}

/* form */
.prospect{position:absolute;left:0;top:1810px;width:1200px;height:735px;background:var(--red)}
.prospect .section-title{color:#fff;top:60px;font-size:31px}
.field{position:absolute;width:300px}
.field label{display:block;color:#fff;font-weight:700;font-size:15px;letter-spacing:.5px;margin-bottom:12px}
.field .input{height:46px;background:#fff;border-radius:3px;font-size:12px;color:#888;padding:0 20px;display:flex;align-items:center;justify-content:space-between}

/* listings */
.card{position:absolute;top:2687px;width:300px;height:443px;background:#fff;box-shadow:0 2px 12px rgba(0,0,0,.15)}
.card .photo{height:177px}
.card .body{padding:16px 17px}
.card h4{font-family:"Lora",serif;color:var(--red);font-size:22px;font-weight:600}
.card .size{font-size:12px;color:#666;margin-top:8px}
.card .price{font-size:19px;font-weight:700;margin-top:12px}
.card .rooms{font-size:12px;color:var(--red);margin-top:16px;display:flex;gap:50px}
.card .addr{display:flex;gap:14px;font-size:12px;color:#444;margin-top:18px;line-height:20px}
.card .btn{position:static;width:128px;height:36px;font-size:13px;margin-top:18px;font-weight:700}

/* community */
.community{position:absolute;left:0;top:3200px;width:1200px;height:512px;background:linear-gradient(180deg,#8fb0d0 0%,#b9c6c9 40%,#8a7d55 70%,#3b4a2c 100%)}
.community .brandline{position:absolute;left:372px;top:45px;display:flex;align-items:center;gap:18px}
.community .brandline .mark{width:90px;height:90px;border-radius:50%;background:var(--red)}
.community .brandline span{font-family:"Lora",serif;font-size:41px;line-height:40px;color:var(--red-dark)}
.community h2{position:absolute;left:110px;top:200px;font-family:"Lora",serif;font-size:38px;color:#fff}
.community ul{position:absolute;left:110px;top:266px;list-style:none;color:#fff;font-size:20px}
.community li{line-height:41px;padding-left:26px;position:relative}
.community li::before{content:"";position:absolute;left:0;top:13px;width:10px;height:10px;border-radius:50%;background:#fff}

/* footer */
.footer-col{position:absolute;top:3782px}
.footer-col h5{font-family:"Lora",serif;color:var(--red);font-size:17px;letter-spacing:1px;font-weight:700;margin-bottom:14px}
.footer-col a{display:block;font-size:14px;color:#444;line-height:26px;text-decoration:none}
.footer-col p{font-size:14px;color:#444;line-height:26px}
.social{position:absolute;left:100px;top:3904px;display:flex;gap:9px}
.social i{width:26px;height:26px;border-radius:50%;background:var(--red)}
.contact-item{position:absolute;display:flex;align-items:center;gap:12px;font-size:15px;color:#333;line-height:21px}
.badge{position:absolute;top:4097px;height:28px;background:#777}
</style>
</head>
<body>

<header class="site-header">
  <div class="brand"><div class="mark"></div><div class="name">BRIGHTHOLD</div><div class="sub">PROPERTY MANAGEMENT &amp; SERVICES</div></div>
  <div class="btn" style="left:541px;top:18px;width:206px;height:43px">Book An Appointment</div>
  <div class="btn" style="left:771px;top:18px;width:147px;height:43px;font-size:18px">
    <svg width="20" height="15" viewBox="0 0 20 15"><rect x="1" y="1" width="18" height="13" rx="1" fill="#fff"/><path d="M1 2l9 7 9-7" stroke="#a50d12" stroke-width="2" fill="none"/></svg>Contact</div>
  <div class="btn" style="left:942px;top:18px;width:146px;height:43px;font-size:18px">
    <svg width="18" height="18" viewBox="0 0 18 18"><circle cx="9" cy="5" r="4.5" fill="#fff"/><path d="M1 18c0-6 16-6 16 0z" fill="#fff"/></svg>LOGIN</div>
  <nav class="main-nav"><span>Home</span><span>Listings</span><span>Owners</span><span>Prospect Tenants</span><span>About</span><span>Community</span><span>Mortgage Info</span></nav>
</header>

<section class="hero" role="img" aria-label="Night view of a lit river bridge and city skyline">
  <div class="hero-box">
    <h1>CALL TODAY</h1>
    <p>&amp; Get 1 Month Property Management<br>Fee Off. $120 Value!!</p>
    <div class="btn" style="left:181px;top:206px;width:206px;height:43px">Book An Appointment</div>
  </div>
  <div class="dots"><i></i><i></i><i class="on"></i><i></i><i></i></div>
</section>

<h2 class="section-title" style="top:822px;font-size:31px">INFORMATION OF SERVICES</h2>
<div class="service" style="left:99px">
  <svg width="180" height="180" viewBox="0 0 180 180"><rect x="36" y="36" width="108" height="108" transform="rotate(45 90 90)" fill="none" stroke="#a50d12" stroke-width="3"/><path d="M66 92l24-22 24 22M72 87v27h36V87M84 114V98h12v16" fill="none" stroke="#a50d12" stroke-width="3"/></svg>
  <h3>RESIDENTS</h3></div>
<div class="service" style="left:365px">
  <svg width="180" height="180" viewBox="0 0 180 180"><rect x="36" y="36" width="108" height="108" transform="rotate(45 90 90)" fill="none" stroke="#a50d12" stroke-width="3"/><path d="M70 114V82h16v32M86 114V70h24v44M66 114h48M92 78h4M100 78h4M92 88h4M100 88h4M92 98h4M100 98h4M75 90h6M75 100h6" fill="none" stroke="#a50d12" stroke-width="2.5"/></svg>
  <h3>PROPERTY</h3></div>
<div class="service" style="left:629px">
  <svg width="180" height="180" viewBox="0 0 180 180"><rect x="36" y="36" width="108" height="108" transform="rotate(45 90 90)" fill="none" stroke="#a50d12" stroke-width="3"/><path d="M68 114V86l22-16 22 16v28zM84 114V98h12v16M86 86h8" fill="none" stroke="#a50d12" stroke-width="3"/></svg>
  <h3>HOME</h3></div>
<div class="service" style="left:900px">
  <svg width="180" height="180" viewBox="0 0 180 180"><rect x="36" y="36" width="108" height="108" transform="rotate(45 90 90)" fill="none" stroke="#a50d12" stroke-width="3"/><path d="M64 88l26-18 26 18M68 86v26h44V86M74 94h8v8h-8zM98 94h8v8h-8zM86 112V96h8v16" fill="none" stroke="#a50d12" stroke-width="2.5"/></svg>
  <h3>RENTAL PROPERTY</h3></div>

<section class="about">
  <div class="about-photo" role="img" aria-label="Family walking into their new home, a child running ahead"></div>
  <div class="about-text">
    <h2>ABOUT US</h2>
    <p>Our vision for Brighthold Property Management is to provide the best Property Management Services to the Sacramento and surrounding areas. I am focused on providing a more personalized service to you and your tenants. This means we are a one-stop-shop. You only deal with me, no middle guy, so no time is wasted.</p>
    <p style="margin-top:24px">Brighthold Property Management is operated and owned by me Thomas Whitaker. I have over 10 years of experience in property management combined with real estate appraising and understand the importance of 'return on investment.'</p>
    <p class="cta">IF YOU WOULD LIKE TO TRY MY SERVICE OR IF YOU HAVE <em>ANY QUESTIONS, PLEASE CALL ME AT (916) 555-0142</em>. THANK YOU</p>
    <div class="btn" style="position:relative;width:162px;height:44px;margin-top:22px">CLICK HERE</div>
  </div>
</section>

<section class="prospect">
  <h2 class="section-title">PROSPECT INPUT INFOMATION</h2>
  <div class="field" style="left:110px;top:137px"><label>CITY</label><div class="input">Austria</div></div>
  <div class="field" style="left:449px;top:137px"><label>STATE</label><div class="input">Illinois</div></div>
  <div class="field" style="left:788px;top:137px"><label>POSTAL CODE</label><div class="input">7684322</div></div>
  <div class="field" style="left:110px;top:247px"><label>TYPE OF PROPERTY</label><div class="input">Purchase<svg width="18" height="10"><path d="M1 1l8 8 8-8" stroke="#555" stroke-width="2" fill="none"/></svg></div></div>
  <div class="field" style="left:449px;top:247px"><label>PROPERY DESIRED</label><div class="input">Owner Occupied<svg width="18" height="10"><path d="M1 1l8 8 8-8" stroke="#555" stroke-width="2" fill="none"/></svg></div></div>
  <div class="field" style="left:788px;top:247px"><label>ADDITIONAL PREFERENCE</label><div class="input">407 - (Good)<svg width="18" height="10"><path d="M1 1l8 8 8-8" stroke="#555" stroke-width="2" fill="none"/></svg></div></div>
  <div class="field" style="left:110px;top:355px;width:978px"><label>OTHER PREFERENCES</label><div class="input" style="height:190px;align-items:flex-start;padding-top:20px">Lorem ipsum dolor sit amet, consectetur adipiscing elit.</div></div>
  <div class="btn btn-ghost" style="left:110px;top:615px;width:163px;height:45px">NEXT PAGE <svg width="14" height="14"><path d="M1 0l13 7-13 7z" fill="#a50d12"/></svg></div>
</section>

<h2 class="section-title" style="top:2603px;font-size:36px">OUR LISTINGS</h2>
<article class="card" style="left:110px">
  <div class="photo" role="img" aria-label="Modern two-storey house at dusk" style="background:linear-gradient(180deg,#6f73a8,#8a7f86 55%,#4a4438)"></div>
  <div class="body"><h4>RESIDENTIAL</h4><div class="size">693 Sq. Ft</div><div class="price">$2,000.00</div>
  <div class="rooms"><span>Bedrooms:2</span><span>Bathrooms:1</span></div>
  <div class="addr"><svg width="22" height="26" viewBox="0 0 22 26"><path d="M11 24s-8-8-8-13a8 8 0 0116 0c0 5-8 13-8 13z" fill="none" stroke="#555" stroke-width="1.6"/><circle cx="11" cy="11" r="3" fill="none" stroke="#555" stroke-width="1.6"/></svg><span>3418 Elmcrest Ave Oakland, CA 94621<br>Alameda, US</span></div>
  <div class="btn">CLICK HERE</div></div>
</article>
<article class="card" style="left:449px">
  <div class="photo" role="img" aria-label="White house with a for-rent sign on the lawn" style="background:linear-gradient(180deg,#9cc1e2,#e9e6df 50%,#b5322d 90%)"></div>
  <div class="body"><h4>RESIDENTIAL RENTED</h4><div class="size">693 Sq. Ft</div><div class="price">$1,695.00</div>
  <div class="rooms"><span>Bedrooms:3</span><span>Bathrooms:1</span></div>
  <div class="addr"><svg width="22" height="26" viewBox="0 0 22 26"><path d="M11 24s-8-8-8-13a8 8 0 0116 0c0 5-8 13-8 13z" fill="none" stroke="#555" stroke-width="1.6"/><circle cx="11" cy="11" r="3" fill="none" stroke="#555" stroke-width="1.6"/></svg><span>2290 Maple Row #4 Sacramento, CA 95818<br>Sacramento, US</span></div>
  <div class="btn">CLICK HERE</div></div>
</article>
<article class="card" style="left:788px">
  <div class="photo" role="img" aria-label="Hands with a tablet beside a small house model on plans" style="background:linear-gradient(160deg,#3c4652,#9aa1a8 50%,#e8e6e3)"></div>
  <div class="body"><h4>RESIDENTIAL</h4><div class="size">1,350 Sq. Ft.</div><div class="price">$4,300.00</div>
  <div class="rooms"><span>Bedrooms:2</span><span>Bathrooms:1</span></div>
  <div class="addr"><svg width="22" height="26" viewBox="0 0 22 26"><path d="M11 24s-8-8-8-13a8 8 0 0116 0c0 5-8 13-8 13z" fill="none" stroke="#555" stroke-width="1.6"/><circle cx="11" cy="11" r="3" fill="none" stroke="#555" stroke-width="1.6"/></svg><span>7715 Birchwood Ave #3 Carmichael, CA 95608<br>Sacramento, US</span></div>
  <div class="btn">CLICK HERE</div></div>
</article>

<section class="community" role="img" aria-label="Sacramento riverfront skyline with a stepped pyramid building">
  <div class="brandline"><div class="mark"></div><span>Brighthold Property<br>Management Inc.</span></div>
  <h2>COMMUNITY RESOURCES</h2>
  <ul><li>NEIGHBORLY COMMUNITIES</li><li>REGIONAL CENTER FOR SCHOOL STATS</li><li>BRIGHTSCHOOLGUIDE.NET</li></ul>
  <div class="btn btn-ghost" style="left:110px;top:390px;width:163px;height:45px">CLICK HERE <svg width="14" height="14"><path d="M1 0l13 7-13 7z" fill="#a50d12"/></svg></div>
</section>

<footer>
  <div class="brand" style="top:3790px"><div class="mark"></div><div class="name">BRIGHTHOLD</div><div class="sub">PROPERTY MANAGEMENT &amp; SERVICES</div></div>
  <div class="social"><i></i><i></i><i></i><i></i><i></i></div>
  <div class="footer-col" style="left:336px"><h5>INFORMATIONS</h5><a>Home</a><a>Listings</a><a>Owners</a><a>Prospect Tenants</a><a>About</a><a>Community</a></div>
  <div class="footer-col" style="left:541px"><h5>CUSTOMER SERVICES</h5><a>Privacy Policy</a><a>Terms &amp; Conditions</a><a>Shipping &amp; Returns</a><a>Help &amp; FAQs</a><a>Refund Policy</a><a>Customer Service</a></div>
  <div class="footer-col" style="left:796px;width:270px"><h5>NEWSLETTER</h5><p>Lorem ipsum dolor sit amet, consectetur adipiscing elit, sed do eiusmod tempor incididunt ut labore et dolore magna aliqua. Ut enim ad minim</p>
    <div style="display:flex;margin-top:16px;height:34px;width:257px;background:var(--red);color:#fff;font-size:12px;align-items:center"><span style="flex:1;padding-left:16px">Enter Email Id</span><span style="background:#111;height:100%;padding:0 12px;display:flex;align-items:center;font-size:11px;font-weight:700">SUBSCRIBE</span></div></div>
  <div class="contact-item" style="left:110px;top:3995px"><svg width="34" height="34" viewBox="0 0 34 34"><circle cx="17" cy="17" r="15" fill="none" stroke="#a50d12" stroke-width="3"/><path d="M11 10l4 0 2 5-3 2c1 3 3 5 6 6l2-3 5 2v4c-9 1-17-7-16-16z" fill="#a50d12"/></svg>(916) 555-0142</div>
  <div class="contact-item" style="left:484px;top:3988px"><svg width="30" height="36" viewBox="0 0 30 36"><path d="M15 34S3 22 3 14a12 12 0 0124 0c0 8-12 20-12 20z" fill="#a50d12"/><circle cx="15" cy="14" r="4.5" fill="#fff"/></svg>4870 Larkmoor Rd. #212<br>Sacramento , CA 95822</div>
  <div class="contact-item" style="left:926px;top:3995px"><svg width="34" height="34" viewBox="0 0 34 34"><circle cx="17" cy="17" r="15" fill="none" stroke="#a50d12" stroke-width="3"/><path d="M11 10l4 0 2 5-3 2c1 3 3 5 6 6l2-3 5 2v4c-9 1-17-7-16-16z" fill="#a50d12"/></svg>(916) 555-0142</div>
  <div class="abs" style="left:110px;top:4078px;width:978px;height:1px;background:#999"></div>
  <div class="badge" style="left:130px;width:36px"></div>
  <div class="badge" style="left:193px;width:60px"></div>
  <div class="badge" style="left:277px;width:26px"></div>
  <div class="abs" style="left:0;width:1200px;top:4102px;text-align:center;font-size:14px;color:#333">Copyright© 2024 BRIGHTHOLD PROPERTY MANAGEMENT INC.</div>
  <div class="abs" style="left:1141px;top:4092px;font-size:12px;color:#333">C75</div>
</footer>

</body>
</html>
```